Business Card for Multi-Brand Sportswear Company

We are looking for a business card which represents our company and the multiple brands within it.

The company: Fen Athletics (LTD)
The brands: Fen, TavaPuni, ElmStretch, Grit and Rain

Employees using these cards would be representing Fen Athletics, rather than any of the individual brands. You will see a current design within the uploaded files, to give some inspiration. The actual text of the brands is not necessary, but the logos should be on there is some format.

Our creative minds on this are stretched, so we are looking for someone to make this their own, and show us what a good business card should look like.

We may like to get these printed with spot gloss, so keep that in mind with your designs.

www.fenathletics.co.uk

Industry/Entity Type

Business

Contact Information for Business Card

Leo Pemberton-Hale
Operations Manager
(+44) 1632 960 418
Leo@fenathletics.co.uk
www.fenathletics.co.uk

Font styles to use
Sans Serif
Other font styles liked:
• Eurostile

Colors
ffffff

Requirements
Nice to have
• Dark (black) background

```html
<!DOCTYPE html>
<html lang="en">
<head>
<meta charset="utf-8">
<title>Fen Athletics — Business Card</title>
<link rel="stylesheet" href="https://fonts.googleapis.com/css2?family=Arimo:wght@400;700&display=swap">
<style>
  :root {
    --stage: #d3d3d3;
    --card-dark: #403e3d;
    --card-light: #ffffff;
    --ink: #111111;
    --ink-on-dark: #ffffff;
    --text: #1f1f1f;
    --accent: #e3161e;
    --divider: #ec8a8a;
    --badge-violet: #5e4e66;
    --badge-grey: #9a9a9a;
  }
  * { margin: 0; padding: 0; box-sizing: border-box; }
  html, body {
    width: 1167px;
    height: 1200px;
    overflow: hidden;
    background: var(--stage);
    font-family: "Arimo", Arial, sans-serif;
  }
  .canvas { position: relative; width: 1167px; height: 1200px; }

  .card { position: absolute; box-shadow: 0 6px 14px rgba(0,0,0,0.22); }
  .card--back { left: 165px; top: 106px; width: 798px; height: 444px; background: var(--card-dark); }
  .card--front { left: 157px; top: 616px; width: 809px; height: 445px; background: var(--card-light); }

  .wordmark {
    position: absolute;
    display: flex;
    align-items: center;
    color: var(--ink);
    font-weight: 700;
    line-height: 1.15;
    white-space: nowrap;
    letter-spacing: 0.5px;
  }
  .wordmark__square { background: var(--accent); flex: none; }
  .card--back .wordmark { left: 56px; top: 180px; font-size: 90px; gap: 22px; color: var(--ink-on-dark); }
  .card--back .wordmark__square { width: 28px; height: 28px; }
  .card--front .wordmark { left: 37px; top: 172px; font-size: 50px; gap: 12px; }
  .card--front .wordmark__square { width: 16px; height: 16px; }

  .brand-badges { position: absolute; left: 464px; top: 364px; width: 270px; height: 46px; }
  .badge { position: absolute; }
  .badge--violet { left: 0; top: 1px; width: 64px; height: 43px; border-radius: 4px; background: var(--badge-violet); }
  .badge--ring { left: 102px; top: 0; width: 43px; height: 43px; border-radius: 50%; border: 3px solid var(--badge-grey); }
  .badge--red { left: 218px; top: 2px; width: 42px; height: 42px; border-radius: 6px; border: 3px solid var(--accent); }

  .divider { position: absolute; left: 429px; top: 117px; width: 2px; height: 218px; background: var(--divider); }

  .contact { position: absolute; left: 458px; top: 124px; }
  .contact__name { color: var(--accent); font-size: 24px; font-weight: 400; line-height: 1; white-space: nowrap; }
  .contact__role { margin: 8px 0 0 41px; color: var(--text); font-size: 18px; line-height: 1; }
  .contact__list { list-style: none; margin-top: 38px; }
  .contact__item { display: flex; align-items: center; height: 28px; color: var(--text); font-size: 17px; white-space: nowrap; }
  .contact__icon { width: 18px; height: 18px; margin-right: 15px; flex: none; }
</style>
</head>
<body>
<main class="canvas">

  <section class="card card--back" aria-label="Business card back">
    <div class="wordmark"><span class="wordmark__square"></span>Fen Athletics</div>
    <div class="brand-badges" aria-label="Group brands">
      <span class="badge badge--violet"></span>
      <span class="badge badge--ring"></span>
      <span class="badge badge--red"></span>
    </div>
  </section>

  <section class="card card--front" aria-label="Business card front">
    <div class="wordmark"><span class="wordmark__square"></span>Fen Athletics</div>
    <div class="divider"></div>
    <div class="contact">
      <h1 class="contact__name">Leo Pemberton-Hale</h1>
      <p class="contact__role">Operations Manager</p>
      <ul class="contact__list">
        <li class="contact__item">
          <svg class="contact__icon" viewBox="0 0 18 18" aria-hidden="true"><path d="M9 1.5a5.5 5.5 0 0 0-5.5 5.5c0 4 5.5 9.5 5.5 9.5s5.5-5.5 5.5-9.5A5.5 5.5 0 0 0 9 1.5z" fill="#e3161e"/><circle cx="9" cy="7" r="2" fill="#fff"/></svg>
          Your Address
        </li>
        <li class="contact__item">
          <svg class="contact__icon" viewBox="0 0 18 18" aria-hidden="true"><circle cx="9" cy="9" r="7.5" fill="none" stroke="#e3161e" stroke-width="1.4"/><path d="M6.4 5.2l1.4-.3.8 2-1 .8a5 5 0 0 0 2.7 2.7l.8-1 2 .8-.3 1.4c-3.6.2-6.6-2.8-6.4-6.4z" fill="#e3161e"/></svg>
          (+44) 1632 960 418
        </li>
        <li class="contact__item">
          <svg class="contact__icon" viewBox="0 0 18 18" aria-hidden="true"><rect x="2" y="4" width="14" height="10" fill="none" stroke="#e3161e" stroke-width="1.4"/><path d="M2 4l7 5.5L16 4" fill="none" stroke="#e3161e" stroke-width="1.4"/></svg>
          Leo@fenathletics.co.uk
        </li>
        <li class="contact__item">
          <svg class="contact__icon" viewBox="0 0 18 18" aria-hidden="true"><g fill="none" stroke="#e3161e" stroke-width="1.3"><circle cx="9" cy="9" r="7"/><ellipse cx="9" cy="9" rx="3" ry="7"/><path d="M2 9h14M3 5.5h12M3 12.5h12"/></g></svg>
          www.fenathletics.co.uk
        </li>
      </ul>
    </div>
  </section>

</main>
</body>
</html>
```